International oil and gas consultancy needs a business card design

We need a business card design for a new oil and gas consultancy business based in Perth Australia. This is a professional services business and needs a moderately conservative type of business card. The business card also needs to be simple and uncluttered. The colour of the business logo is dark red (see attached file).
The front of the card should have a white background and mainly black lettering and perhaps some use of dark red and/or grey (your choice).
The back of the card should have a light grey background with dark red, black and or both dark red & black lettering (your choice).
Please find attached a clear brief of how I would like the business card designed.
Updates

Hello Everyone, I have slightly modified the brief. The main change is to incorporate some dark red and grey colours into the card, while still keeping the black lettering dominant. I have made the changes in the attached detailed brief document. Regards

Please note, the front of the card must say Harbour Ledger Services (in addition to the logo).

Industry/Entity Type

Conservative

Requirements
Must have
• brief has been updated. please refer to attachment for details.

Front of the card MUST say Harbour Ledger Services (in addition to the logo)

```html
<!DOCTYPE html>
<html lang="en">
<head>
<meta charset="utf-8">
<title>Harbour Ledger Services – Business Card</title>
<link rel="stylesheet" href="https://fonts.googleapis.com/css2?family=Arimo:wght@400;700&display=swap">
<style>
  :root {
    --stage: #e6e6e8;
    --card-white: #ffffff;
    --brand-red: #9a1c21;
    --brand-red-deep: #861519;
    --ink: #1a1a1a;
    --ink-soft: #333333;
    --on-red: #ffffff;
    --card-shadow: rgba(0, 0, 0, 0.28);
  }
  * { box-sizing: border-box; margin: 0; padding: 0; }
  html, body {
    width: 1200px;
    height: 600px;
    overflow: hidden;
  }
  body {
    background: var(--stage);
    font-family: "Arimo", Arial, sans-serif;
    display: flex;
    align-items: center;
    justify-content: center;
    gap: 60px;
  }
  .card {
    position: relative;
    width: 500px;
    height: 286px;
    box-shadow: 4px 6px 14px var(--card-shadow);
    overflow: hidden;
  }

  /* Front */
  .card--front { background: var(--card-white); color: var(--ink); }
  .card--front .brand-name {
    position: absolute;
    left: 34px;
    top: 46px;
    font-size: 17px;
    font-weight: 700;
    letter-spacing: 0.4px;
    color: var(--brand-red);
    text-transform: uppercase;
  }
  .card--front .holder {
    position: absolute;
    left: 270px;
    top: 118px;
    width: 200px;
  }
  .holder-name {
    font-size: 16px;
    font-weight: 700;
    text-align: right;
    margin-bottom: 16px;
  }
  .holder-region {
    font-size: 11px;
    color: var(--ink-soft);
  }
  .contact-list {
    position: absolute;
    left: 290px;
    top: 212px;
    list-style: none;
    font-size: 11px;
    line-height: 15px;
    color: var(--ink-soft);
  }

  /* Back */
  .card--back {
    background: linear-gradient(160deg, var(--brand-red) 0%, var(--brand-red-deep) 100%);
    color: var(--on-red);
    text-align: center;
  }
  .card--back .brand-name {
    position: absolute;
    left: 0; right: 0;
    top: 72px;
    padding-left: 60px;
    font-size: 19px;
    font-weight: 700;
    letter-spacing: 0.4px;
    text-transform: uppercase;
  }
  .card--back .brand-rule {
    position: absolute;
    left: 220px;
    top: 102px;
    width: 220px;
    height: 1px;
    background: var(--on-red);
  }
  .tagline {
    position: absolute;
    left: 0; right: 0;
    top: 114px;
    padding-left: 60px;
    font-size: 12px;
    line-height: 15px;
  }
  .service-list {
    position: absolute;
    left: 22px;
    right: 22px;
    bottom: 22px;
    display: flex;
    justify-content: space-between;
    list-style: none;
    font-size: 12px;
  }
  .service-list li {
    display: flex;
    align-items: center;
    gap: 6px;
  }
  .service-list li::before {
    content: "";
    width: 6px;
    height: 6px;
    border-radius: 50%;
    background: var(--on-red);
  }
</style>
</head>
<body>
  <article class="card card--front" aria-label="Business card front">
    <p class="brand-name">Harbour Ledger Services</p>
    <div class="holder">
      <p class="holder-name">Reid Calloway</p>
      <p class="holder-region">Australasia and South East Asia</p>
    </div>
    <ul class="contact-list">
      <li>+61 (0)408 316 592</li>
      <li>reid@harbourledger.com</li>
      <li>www.harbourledger.com</li>
    </ul>
  </article>

  <article class="card card--back" aria-label="Business card back">
    <p class="brand-name">Harbour Ledger Services</p>
    <span class="brand-rule"></span>
    <p class="tagline">Specialist Financial Consultants<br>to the Oil and Gas Industry</p>
    <ul class="service-list">
      <li>Joint Venture Audits</li>
      <li>Contract Audits</li>
      <li>Operational Audits</li>
    </ul>
  </article>
</body>
</html>
```